Walk Beside The River

Business Card design

Target Market(s)

People who require support in the commnity

Industry/Entity Type

Mental Health Support

Contact Information for Business Card

Mental Health Support Rosalind Tavener walkbesidetheriver@mailcove.com.au 0481 637 092 PO Box 926 Kestrel Bay VIC 3941

Colors
6B429C
8869AF
B7A5CE
E3DAEB
F3F0F8

Requirements
Must have
• Logo & details listed above
Should not have
• No red or orange

```html
<!DOCTYPE html>
<html lang="en">
<head>
<meta charset="utf-8">
<title>Walk Beside The River – Business Card</title>
<link rel="stylesheet" href="https://fonts.googleapis.com/css2?family=Open+Sans:wght@400;600&display=swap">
<style>
  :root {
    --backdrop: #2a292e;
    --card: #1f1e25;
    --card-edge: #17161c;
    --brand-purple: #6b429c;
    --accent-yellow: #e9e43a;
    --text-light: #f1eff6;
    --emboss: #2d2b35;
  }
  * { margin: 0; padding: 0; box-sizing: border-box; }
  html, body { width: 1200px; height: 780px; overflow: hidden; }
  body {
    background: var(--backdrop);
    font-family: "Open Sans", Arial, sans-serif;
    display: flex;
    align-items: center;
    justify-content: center;
    gap: 40px;
  }
  .card {
    position: relative;
    width: 540px;
    height: 315px;
    background: var(--card);
    border: 1px solid var(--card-edge);
    overflow: hidden;
  }
  .brand {
    position: absolute;
    top: 26px;
    right: 26px;
    display: flex;
    align-items: center;
    gap: 12px;
  }
  .brand-dot {
    width: 46px; height: 46px;
    border-radius: 50%;
    background: var(--brand-purple);
  }
  .brand-name {
    color: var(--text-light);
    font-weight: 600;
    font-size: 17px;
    letter-spacing: 0.04em;
  }
  .details {
    position: absolute;
    left: 30px;
    top: 118px;
    color: var(--text-light);
  }
  .service { font-size: 19px; line-height: 1.3; }
  .person { font-size: 19px; line-height: 1.3; margin-bottom: 6px; }
  .contact-list { list-style: none; }
  .contact-list li {
    display: flex;
    align-items: center;
    gap: 8px;
    font-size: 17px;
    line-height: 1.45;
  }
  .contact-list svg { width: 15px; height: 15px; flex: none; }
  .back { display: flex; align-items: center; justify-content: center; gap: 16px; }
  .back-dot {
    width: 70px; height: 70px;
    border-radius: 50%;
    background: var(--emboss);
  }
  .back-name {
    color: var(--emboss);
    font-weight: 600;
    font-size: 28px;
    letter-spacing: 0.04em;
  }
</style>
</head>
<body>
  <section class="card front">
    <div class="brand">
      <span class="brand-dot"></span>
      <span class="brand-name">Walk Beside The River</span>
    </div>
    <div class="details">
      <p class="service">Mental Health Support</p>
      <p class="person">Rosalind Tavener</p>
      <ul class="contact-list">
        <li>
          <svg viewBox="0 0 16 16" aria-hidden="true"><path fill="var(--accent-yellow)" d="M4 1.5l2.2 3-1.4 1.5c.8 1.8 2.3 3.3 4.2 4.2l1.5-1.4 3 2.2-1 2.5C7 13.5 2.5 9 2 2.5z"/></svg>
          0481 637 092
        </li>
        <li>
          <svg viewBox="0 0 16 16" aria-hidden="true"><rect x="1.5" y="3.5" width="13" height="9" fill="none" stroke="var(--accent-yellow)" stroke-width="1.6"/><path d="M1.5 3.5L8 9l6.5-5.5" fill="none" stroke="var(--accent-yellow)" stroke-width="1.6"/></svg>
          walkbesidetheriver@mailcove.com.au
        </li>
        <li>
          <svg viewBox="0 0 16 16" aria-hidden="true"><path fill="var(--accent-yellow)" d="M8 1a5 5 0 0 0-5 5c0 3.5 5 9 5 9s5-5.5 5-9a5 5 0 0 0-5-5zm0 7a2 2 0 1 1 0-4 2 2 0 0 1 0 4z"/></svg>
          PO Box 926 Kestrel Bay VIC 3941
        </li>
      </ul>
    </div>
  </section>

  <section class="card back">
    <span class="back-dot"></span>
    <span class="back-name">Walk Beside The River</span>
  </section>
</body>
</html>
```